Briloran Clear Springs needs a new business card design (we produce and sell pure bottled water)

We need a clean modern design for our new business cards, We have an existing logo which ultimately cannot be changed, however it could be slighty improved and the colours adjusted. We have this existing logo on all of our bottles, vehicles etc.

Our company slogan is "Clear from source to sip".
Along with our relevant company information
(Address, phone, website email etc) we will only be using names and not putting position titles for flexibilty.

We are looking for a clean, minimalist modern design.

You can view our website (if need of an update also!) to see our business.

Industry/Entity Type

Business

Contact Information for Business Card

Staff Name : XXXXXX XXXXXX
Address : 9/41 Tavenor St
Halden Rise QLD 4172
Staff Mobile Number : 04XX XXX XXX
Office Phone Number : 07 3918 2457
Staff Email Address : XXXX@brilorancleargo.com.au
Website : www.brilorancleargo.com.au

Font styles to use
Sans Serif

Colors
cee9f5
33a6d7
0492cd
0455a3
3276b5
85abd2
cedeed

Requirements
Must have
• The ability to edit and change the staff members details as we will need to edit for each respective staff member (7 in total)

```html
<!DOCTYPE html>
<html lang="en">
<head>
<meta charset="utf-8">
<title>Briloran Clear Springs – Business Card</title>
<link href="https://fonts.googleapis.com/css2?family=Source+Sans+3:wght@400;600;700;800&display=swap" rel="stylesheet">
<style>
  :root {
    --stage-top: #242424;
    --stage-bottom: #050505;
    --card-white: #ffffff;
    --brand-blue: #0a4ea3;
    --brand-mid: #0455a3;
    --brand-bright: #1a6fc8;
    --text-dark: #2b2b2b;
    --on-blue: #ffffff;
  }
  * { margin: 0; padding: 0; box-sizing: border-box; }
  html, body { width: 1200px; height: 900px; overflow: hidden; }
  body {
    background: linear-gradient(180deg, var(--stage-top) 0%, #151515 55%, var(--stage-bottom) 100%);
    font-family: "Source Sans 3", "Myriad Pro", Arial, sans-serif;
    position: relative;
  }
  .card {
    position: absolute;
    top: 306px;
    width: 439px;
    height: 271px;
    border-radius: 11px;
    overflow: hidden;
    box-shadow: 0 2px 6px rgba(0,0,0,0.45);
  }
  .card--front { left: 149px; background: var(--card-white); }
  .card--back  { left: 609px; }

  .wordmark {
    position: absolute;
    font-weight: 800;
    line-height: 1;
    text-align: center;
  }
  .wordmark__badge {
    display: block;
    width: 84px; height: 84px;
    border-radius: 50%;
    margin: 0 auto 12px;
  }
  .wordmark__name { display: block; font-size: 34px; letter-spacing: 0.5px; }
  .wordmark__sub  { display: block; font-size: 17px; letter-spacing: 1.5px; margin-top: 3px; }

  .card--front .wordmark { left: 24px; top: 56px; width: 162px; color: var(--brand-blue); }
  .card--front .wordmark__badge { background: var(--brand-bright); }

  .details { position: absolute; left: 214px; top: 46px; color: var(--text-dark); }
  .details__name {
    font-size: 15.5px; font-weight: 600; color: var(--brand-blue);
    letter-spacing: 0.4px; text-transform: uppercase;
  }
  .details__address { margin-top: 19px; font-size: 12.5px; line-height: 16px; }
  .details__contacts { list-style: none; margin-top: 11px; font-size: 12.5px; line-height: 16px; }
  .details__contacts li { display: flex; align-items: center; }
  .details__contacts svg { width: 9px; height: 9px; margin: 0 7px 0 1px; fill: var(--brand-blue); flex: none; }
  .details__slogan {
    margin-top: 12px; font-size: 12.5px; font-weight: 600;
    color: var(--brand-blue); letter-spacing: 0.6px; text-transform: uppercase;
  }

  .card__field {
    position: absolute; inset: 0;
    background: linear-gradient(180deg, var(--brand-bright) 0%, var(--brand-mid) 100%);
  }
  .card--back .wordmark { left: 0; width: 100%; top: 56px; color: var(--on-blue); }
  .card--back .wordmark__badge { background: var(--on-blue); }
</style>
</head>
<body>

  <section class="card card--front" aria-label="Business card front">
    <div class="wordmark">
      <span class="wordmark__badge"></span>
      <span class="wordmark__name">BRILORAN</span>
      <span class="wordmark__sub">CLEAR SPRINGS</span>
    </div>

    <div class="details">
      <p class="details__name">Marcus Ellery</p>
      <p class="details__address">9/41 Tavenor St<br>Halden Rise QLD 4172</p>
      <ul class="details__contacts">
        <li>
          <svg viewBox="0 0 10 10" aria-hidden="true"><path d="M1 3.2C1 2 2.2 1.5 5 1.5S9 2 9 3.2V4H7V3.2H3V4H1Z M2.5 4.5h5L9 8.5H1Z"/></svg>
          0400 517 293
        </li>
        <li>
          <svg viewBox="0 0 10 10" aria-hidden="true"><path d="M3 0.5h4a.8.8 0 0 1 .8.8v7.4a.8.8 0 0 1-.8.8H3a.8.8 0 0 1-.8-.8V1.3A.8.8 0 0 1 3 .5Zm.4 1.2v5.8h3.2V1.7Z"/></svg>
          07 3918 2457
        </li>
        <li>
          <svg viewBox="0 0 10 10" aria-hidden="true"><path d="M.5 2h9v6h-9Zm1 .8L5 5.4l3.5-2.6Z"/></svg>
          info@brilorancleargo.com.au
        </li>
        <li>
          <svg viewBox="0 0 10 10" aria-hidden="true"><circle cx="5" cy="5" r="4.3"/></svg>
          www.brilorancleargo.com.au
        </li>
      </ul>
      <p class="details__slogan">Clear from source to sip</p>
    </div>
  </section>

  <section class="card card--back" aria-label="Business card back">
    <div class="card__field" role="img" aria-label="Blue background with a faint repeating brand pattern"></div>
    <div class="wordmark">
      <span class="wordmark__badge"></span>
      <span class="wordmark__name">BRILORAN</span>
      <span class="wordmark__sub">CLEAR SPRINGS</span>
    </div>
  </section>

</body>
</html>
```